International Medical Company Needs a Website Design for a Support Site

We need a website design for a support site we are doing for ostomates called Bright Returns. We are an international company but this website is for our Australian market.

The website is a support site for people who are living with an Ostomy or Bowel Disease. This is a site where they can read other ostomates' stories and how they are dealing with the fact that they have to wear a pouch everyday.

The URL for our US site is: http://www.brightreturnsite.example/

We need to use the same logo but we have freedom around the color scheme. We are not fond of the brown color scheme used in our US site and are happy for designs to be submitted with alternatives.

• We want the design to be clean, inspiring, modern and inviting.
• We would like to see a design for the mainpage / homepage and one of the subpages
• We only require the PSD / image files (no HTML needed)

Attached to this project is our sitemap, an example wireframe and the logos. We are happy for you to play around with different options and don't have to stick to the layout shown in the wireframe.

If you have any further questions please ask.

Industry/Entity Type

It Company

```html
<!DOCTYPE html>
<html lang="en">
<head>
<meta charset="utf-8">
<title>Bright Returns – Sharing Stories and Giving Hope</title>
<link href="https://fonts.googleapis.com/css2?family=Open+Sans:wght@400;600&display=swap" rel="stylesheet">
<style>
:root{
  --brand-blue:#0a72c4;
  --hero-deep:#0b3c76;
  --hero-light:#0b74b8;
  --bronze:#8f6a32;
  --bronze-text:#8a672c;
  --ink:#444;
  --muted:#666;
  --rule:#cfcfcf;
  --page:#e6e6e6;
  --card:#f1f1f1;
  --card-foot:#dedede;
  --dark-btn:#555;
}
*{box-sizing:border-box;margin:0;padding:0}
html,body{width:1200px;height:1153px;overflow:hidden}
body{position:relative;font-family:"Open Sans",Arial,sans-serif;color:var(--ink);
  background:repeating-linear-gradient(45deg,#e9e9e9 0 2px,#e3e3e3 2px 4px)}
.site-header{position:absolute;left:0;top:0;width:1200px;height:142px;background:#fff}
.header-rule{position:absolute;top:94px;height:1px;background:var(--rule)}
.brand{position:absolute;left:112px;top:10px;width:190px;height:126px;display:flex;align-items:flex-end;gap:8px;padding-bottom:10px}
.brand-mark{width:12px;height:12px;border-radius:50%;background:var(--bronze);margin-bottom:4px}
.brand-name{font-size:17px;font-weight:600;letter-spacing:1.5px;color:var(--bronze-text);text-transform:uppercase}
.btn{position:absolute;display:flex;align-items:center;justify-content:center;color:#fff;font-size:13px;text-transform:uppercase;border-radius:3px}
.btn-share-top{left:905px;top:11px;width:123px;height:37px;background:var(--brand-blue)}
.btn-region{left:1035px;top:11px;width:83px;height:37px;background:var(--dark-btn);gap:6px;border:1px solid #444}
.flag{width:20px;height:12px;background:repeating-linear-gradient(180deg,#c33 0 2px,#fff 2px 4px);position:relative}
.flag::before{content:"";position:absolute;left:0;top:0;width:9px;height:7px;background:#2b4b8f}
.caret{width:0;height:0;border-left:5px solid transparent;border-right:5px solid transparent;border-top:6px solid #fff;margin-left:4px}
.main-nav{position:absolute;top:95px;left:0;height:47px;width:1200px}
.nav-item{position:absolute;top:0;height:47px;display:flex;align-items:center;font-size:13.3px;text-transform:uppercase;color:#444}
.nav-item.is-active{background:var(--bronze);color:#fff;justify-content:center;width:90px}
.content{position:absolute;left:82px;top:158px;width:1036px;height:922px;background:#fff}
.hero{position:absolute;left:0;top:0;width:1036px;height:441px;
  background:radial-gradient(ellipse 520px 380px at 300px 250px,var(--hero-light),var(--hero-deep))}
.hero-title{position:absolute;left:46px;top:126px;font-size:22.5px;font-weight:400;color:#fff;text-transform:uppercase}
.hero-text{position:absolute;left:47px;top:168px;width:380px;font-size:17.5px;line-height:20.5px;color:#fff}
.btn-share-hero{left:47px;top:244px;width:123px;height:36px;background:var(--bronze)}
.hero-photo{position:absolute;left:473px;top:26px;width:534px;height:361px;
  background:linear-gradient(135deg,#cfe0d2 0%,#f4f2ee 40%,#ece7df 75%,#d9d2c6 100%)}
.dots{position:absolute;top:410px;left:469px;display:flex;gap:15px;align-items:center}
.dot{width:11px;height:11px;border-radius:50%;background:#7fb3dc}
.dot.is-current{width:15px;height:15px;background:transparent;border:2px solid #a9cde9}
.card{position:absolute;top:488px;width:307px;height:365px;background:var(--card);text-align:center}
.card-photo{width:100%;height:174px}
.card-title{margin-top:26px;font-size:16px;font-weight:400;text-transform:uppercase;color:#444}
.card-text{margin:13px auto 0;width:270px;font-size:12.5px;line-height:16px;color:var(--muted)}
.card-more{position:absolute;left:0;bottom:0;width:100%;height:41px;background:var(--card-foot);display:flex;align-items:center;justify-content:center;font-size:13px;color:var(--bronze-text)}
.photo-sea{background:linear-gradient(180deg,#8fa9c4 0%,#5a7fa3 35%,#2f4f73 60%,#d8c9a0 100%)}
.photo-home{background:linear-gradient(135deg,#f1e6cf 0%,#c98e4b 45%,#4a3a2d 100%)}
.photo-touch{background:linear-gradient(120deg,#6b8fb4 0%,#c7d3df 55%,#8ea6bf 100%)}
.site-footer{position:absolute;left:82px;top:1094px;width:1036px;height:20px;font-size:11px;color:var(--muted);text-transform:uppercase}
.copyright{position:absolute;left:0;top:0}
.legal{position:absolute;right:116px;top:0}
.social{position:absolute;right:0;top:-9px;display:flex;gap:5px}
.social span{width:28px;height:28px;border-radius:50%;background:#777;display:block}
</style>
</head>
<body>
<header class="site-header">
  <div class="header-rule" style="left:0;width:102px"></div>
  <div class="header-rule" style="left:324px;width:876px"></div>
  <div class="brand"><span class="brand-mark"></span><span class="brand-name">Bright Returns</span></div>
  <a class="btn btn-share-top">Share a Story</a>
  <a class="btn btn-region"><span class="flag"></span>US<span class="caret"></span></a>
  <nav class="main-nav">
    <a class="nav-item is-active" style="left:324px">About Us</a>
    <a class="nav-item" style="left:428px">Personal Stories</a>
    <a class="nav-item" style="left:578px">Awards Programs</a>
    <a class="nav-item" style="left:737px">Tips for Living</a>
    <a class="nav-item" style="left:866px">News</a>
    <a class="nav-item" style="left:930px">Resources</a>
    <a class="nav-item" style="left:1032px">Contact Us</a>
  </nav>
</header>

<main class="content">
  <section class="hero">
    <h1 class="hero-title">Sharing Stories and Giving Hope</h1>
    <p class="hero-text">To people around the world who are facing inflammatory bowel disease, colorectal cancer, or have had ostomy sugery</p>
    <a class="btn btn-share-hero">Share a Story</a>
    <div class="hero-photo" role="img" aria-label="Photo of a smiling couple on a white sofa holding a bouquet of flowers"></div>
    <div class="dots"><span class="dot is-current"></span><span class="dot"></span><span class="dot"></span><span class="dot"></span></div>
  </section>

  <article class="card" style="left:48px">
    <div class="card-photo photo-sea" role="img" aria-label="Photo of an older couple standing by the sea"></div>
    <h2 class="card-title">What is a Bright Return</h2>
    <p class="card-text">Habitasse platea dictumst. Suspendisse sollicitudin nisl orci, sit amet varius erat tristique et. Nam elementum, sem vel pel-lentesque ultricies, tellu oncusrisus.</p>
    <a class="card-more">Read more</a>
  </article>
  <article class="card" style="left:364px">
    <div class="card-photo photo-home" role="img" aria-label="Photo of a couple at a laptop in a sunny home"></div>
    <h2 class="card-title">Share a Story</h2>
    <p class="card-text">Habitasse platea dictumst. Suspendisse sollicitudin nisl orci, sit amet varius erat tristique et. Nam elementum, sem vel pel-lentesque ultricies, tellu oncusrisus.</p>
    <a class="card-more">Read more</a>
  </article>
  <article class="card" style="left:681px">
    <div class="card-photo photo-touch" role="img" aria-label="Photo of a finger touching a glowing interface"></div>
    <h2 class="card-title">News</h2>
    <p class="card-text">Habitasse platea dictumst. Suspendisse sollicitudin nisl orci, sit amet varius erat tristique et. Nam elementum, sem vel pel-lentesque ultricies, tellu oncusrisus.</p>
    <a class="card-more">Read more</a>
  </article>
</main>

<footer class="site-footer">
  <span class="copyright">© Copyright 2014 . All rights reserved to Bright Returns</span>
  <span class="legal">Legal Notive | Privacy Policy | Sitemap</span>
  <div class="social"><span></span><span></span><span></span></div>
</footer>
</body>
</html>
```